Tequila Bottle Labels

We are a construction company that bottled our own tequila and would like a unique label for it! We already have our own company logo (linked below) and we want that logo somewhere on the bottle as well- it can be big or small. It was brewed & bottled in Southern California. Ideally it would have the year "2020," "Single Estate," & "100% Agave Azul" somewhere on the label.

Tequila / DMW / 2020

```html
<!DOCTYPE html>
<html lang="en">
<head>
<meta charset="utf-8">
<title>DMW Tequila Label</title>
<link href="https://fonts.googleapis.com/css2?family=Abril+Fatface&family=Rye&family=Oswald:wght@500;600&family=Old+Standard+TT:wght@400;700&family=Playfair+Display+SC:wght@700&display=swap" rel="stylesheet">
<style>
  :root {
    --backdrop: #e9e9e9;
    --ink: #151412;
    --paper: #dcc7a0;
    --paper-deep: #cbb286;
    --paper-band: #bfa67a;
  }
  html, body {
    margin: 0;
    padding: 0;
    width: 1200px;
    height: 1027px;
    overflow: hidden;
    background: var(--backdrop);
  }
  .label {
    position: absolute;
    left: 271px;
    top: 63px;
    width: 657px;
    height: 900px;
    background: var(--ink);
  }
  .label__paper {
    position: absolute;
    left: 40px;
    top: 27px;
    width: 578px;
    height: 843px;
    background: linear-gradient(180deg, var(--paper) 0%, var(--paper-deep) 100%);
  }
  .label__border-band {
    position: absolute;
    inset: 8px;
    border: 10px solid var(--paper-band);
    outline: 1.5px solid var(--ink);
    outline-offset: -1px;
  }
  .label__border-inner {
    position: absolute;
    inset: 20px;
    border: 1.5px solid var(--ink);
  }
  .art {
    position: absolute;
    border-radius: 4px;
  }
  .art--sun { left: 48px; top: 38px; width: 102px; height: 120px; background: radial-gradient(circle, rgba(21,20,18,0.35) 0%, rgba(21,20,18,0) 70%); }
  .art--agave { left: 218px; top: 222px; width: 143px; height: 78px; background: linear-gradient(180deg, rgba(21,20,18,0.15), rgba(21,20,18,0.55)); }
  .art--flourish { left: 195px; top: 488px; width: 188px; height: 45px; background: linear-gradient(90deg, rgba(21,20,18,0.1), rgba(21,20,18,0.5), rgba(21,20,18,0.1)); }
  .art--swirl-left { left: 20px; top: 608px; width: 210px; height: 75px; background: linear-gradient(90deg, rgba(21,20,18,0.45), rgba(21,20,18,0.08)); }
  .art--swirl-right { left: 348px; top: 608px; width: 210px; height: 75px; background: linear-gradient(270deg, rgba(21,20,18,0.45), rgba(21,20,18,0.08)); }
  .art--base-flourish { left: 125px; top: 805px; width: 285px; height: 10px; background: linear-gradient(90deg, rgba(21,20,18,0), rgba(21,20,18,0.5), rgba(21,20,18,0)); }

  .text {
    position: absolute;
    left: 0;
    width: 100%;
    margin: 0;
    text-align: center;
    color: var(--ink);
    line-height: 1;
  }
  .brand-name {
    top: 32px;
    font-family: "Abril Fatface", serif;
    font-size: 150px;
    letter-spacing: -4px;
  }
  .rule {
    position: absolute;
    left: 244px;
    width: 90px;
    height: 1.5px;
    background: var(--ink);
  }
  .rule--top { top: 182px; }
  .rule--bottom { top: 215px; }
  .estate {
    top: 189px;
    font-family: "Oswald", sans-serif;
    font-weight: 600;
    font-size: 21px;
    letter-spacing: 2px;
  }
  .agave-line {
    top: 310px;
    font-family: "Playfair Display SC", serif;
    font-weight: 700;
    font-size: 27px;
    letter-spacing: 3px;
  }
  .product {
    top: 352px;
    font-family: "Rye", serif;
    font-size: 104px;
    letter-spacing: -2px;
  }
  .vintage {
    position: absolute;
    left: 255px;
    top: 571px;
    width: 68px;
    height: 68px;
    border: 2px solid var(--ink);
    border-radius: 50%;
    box-sizing: border-box;
    display: flex;
    align-items: center;
    justify-content: center;
    font-family: "Old Standard TT", serif;
    font-size: 20px;
    color: var(--ink);
  }
  .origin-intro {
    top: 706px;
    font-family: "Oswald", sans-serif;
    font-weight: 500;
    font-size: 26px;
    transform: scaleX(0.78);
  }
  .origin-place {
    top: 739px;
    font-family: "Oswald", sans-serif;
    font-weight: 600;
    font-size: 36px;
    transform: scaleX(0.78);
  }
  .volume, .strength {
    position: absolute;
    top: 792px;
    font-family: "Old Standard TT", serif;
    font-size: 29px;
    color: var(--ink);
    line-height: 1;
  }
  .volume { left: 26px; }
  .strength { right: 26px; }
</style>
</head>
<body>
  <div class="label">
    <div class="label__paper">
      <div class="label__border-band"></div>
      <div class="label__border-inner"></div>

      <div class="art art--sun" role="img" aria-label="Line drawing of a sun"></div>
      <p class="text brand-name">DMW</p>
      <div class="rule rule--top"></div>
      <p class="text estate">SINGLE ESTATE</p>
      <div class="rule rule--bottom"></div>
      <div class="art art--agave" role="img" aria-label="Blue agave plant illustration"></div>
      <p class="text agave-line">100% AGAVE AZUL</p>
      <p class="text product">TEQUILA</p>
      <div class="art art--flourish" role="img" aria-label="Ornamental scroll flourish"></div>
      <div class="art art--swirl-left" role="img" aria-label="Decorative swirl ornament"></div>
      <div class="vintage">2020</div>
      <div class="art art--swirl-right" role="img" aria-label="Decorative swirl ornament"></div>
      <p class="text origin-intro">BREWED AND BOTTLED IN</p>
      <p class="text origin-place">SOUTHERN CALIFORNIA</p>
      <span class="volume">700ml</span>
      <div class="art art--base-flourish" role="img" aria-label="Thin ornamental flourish line"></div>
      <span class="strength">40%abv.</span>
    </div>
  </div>
</body>
</html>
```